Tinker's Lamp sports bar beer & food menu

We need a menu design for our gastropub sports bar in L.A.'s Sawtelle Neighborhood (Little Osaka). We have a full-bar (hard liquor, craft beer, wine and cocktails) . We have a lunch and dinner menu as well as a happy hour menu. On Sundays we have a seperate menu with brunch items. The design concept is a British pub type of sports bar. We're looking for something different from our existing menu design. Ideally something cleaner and more legible. It should mesh a simple, modern sensibility with the more traditional darkened pub style of our interior design.

You can check out our Voxly page for photos of the interior/exterior:
https://www.reviewhatch.example/biz_photos/tinkers-lamp-los-angeles?tab=interior

You can view our existing menu here:
https://www.reviewhatch.example/biz_photos/tinkers-lamp-los-angeles?tab=menu

If there's an area of the design that can be a little more playful it's our highlighted event schedule so that the events will stand out.

Target Market(s)

Age of 25 and up. Sawtelle is a cultural hub that caters to a younger, moderately affluent crowd.

Industry/Entity Type

Sports Bar

Font styles to use
Sans Serif

Colors

Designer to choose colors to be used in the design.

Requirements
Must have
• Logo, highlighted event schedule (beer pong Monday, trivia Tuesday, taco Tuesday, whiskey Wednesday, karaoke Saturday). The menu should be easy to read in a darkened bar. We'll be printing on standard 8.5x11 in portrait.
Nice to have
• We're trying to have the menu take up as few pages as possible.
Should not have
• We're trying to have the menu take up as few pages as possible. Food photography isn't necessary. A cover isn't necessary. Please avoid clip art of food.

```html
<!DOCTYPE html>
<html lang="en">
<head>
<meta charset="utf-8">
<title>Tinker's Lamp — Menu</title>
<link href="https://fonts.googleapis.com/css2?family=Bebas+Neue&family=Questrial&family=Raleway:ital,wght@0,500;0,600;0,700;1,300&display=swap" rel="stylesheet">
<style>
  :root {
    --paper: #ffffff;
    --ink: #111111;
    --muted: #8a8a8a;
    --tan: #c9a97a;
    --gold: #f5a623;
    --rule: #cfcfcf;
  }
  html, body { margin: 0; padding: 0; overflow: hidden; }
  body { background: var(--paper); }
  .menu {
    position: relative;
    width: 927px;
    height: 1200px;
    overflow: hidden;
    background: var(--paper);
    color: var(--ink);
    font-family: "Questrial", sans-serif;
  }
  .brand {
    position: absolute;
    top: 24px;
    left: 0;
    width: 927px;
    display: flex;
    justify-content: center;
    align-items: center;
    gap: 10px;
  }
  .brand-mark {
    width: 22px;
    height: 22px;
    border-radius: 50%;
    background: var(--gold);
  }
  .brand-text { display: flex; flex-direction: column; align-items: center; }
  .brand-name {
    font-family: "Questrial", sans-serif;
    font-size: 30px;
    line-height: 1;
    color: var(--ink);
  }
  .brand-sub {
    font-family: "Questrial", sans-serif;
    font-size: 7px;
    letter-spacing: 3px;
    color: var(--ink);
    margin-top: 4px;
  }
  .header-rule {
    position: absolute;
    top: 85px;
    left: 60px;
    width: 807px;
    height: 1px;
    background: #dddddd;
  }
  .section-title {
    position: absolute;
    margin: 0;
    font-family: "Bebas Neue", sans-serif;
    font-weight: 400;
    font-size: 50px;
    line-height: 43px;
    letter-spacing: 7px;
    color: var(--tan);
    white-space: nowrap;
  }
  .section-title .small { font-size: 34px; letter-spacing: 3px; }
  .item { position: absolute; }
  .item-name {
    margin: 0;
    font-family: "Questrial", sans-serif;
    font-size: 17.5px;
    letter-spacing: 0.8px;
    line-height: 22px;
    color: var(--ink);
    font-weight: 400;
    -webkit-text-stroke: 0.3px var(--ink);
    white-space: nowrap;
  }
  .item-desc {
    margin: 3px 0 0;
    font-family: "Raleway", sans-serif;
    font-style: italic;
    font-weight: 300;
    font-size: 12px;
    line-height: 19.5px;
    color: var(--muted);
  }
  .price {
    position: absolute;
    top: -2px;
    font-family: "Raleway", sans-serif;
    font-weight: 600;
    font-size: 21px;
    color: var(--gold);
  }
  .price sup { font-size: 14px; vertical-align: 3px; }
  .divider {
    position: absolute;
    width: 115px;
    height: 1px;
    background: var(--rule);
  }
  .col-left .item { left: 60px; width: 360px; }
  .col-left .price { left: 325px; }
  .col-left .item-desc { width: 345px; }
  .col-left .divider { left: 60px; }
  .col-right .item { left: 474px; width: 390px; }
  .col-right .price { left: 325px; }
  .col-right .item-desc { width: 385px; }
  .col-right .divider { left: 474px; }
  .frame { position: absolute; top: 0; left: 0; }
  .event-band {
    position: absolute;
    left: 207px;
    top: 1187px;
    width: 513px;
    height: 13px;
    background: var(--tan);
    display: flex;
    justify-content: space-evenly;
    align-items: center;
    font-family: "Raleway", sans-serif;
    font-weight: 700;
    font-size: 8px;
    letter-spacing: 1.2px;
    color: var(--paper);
    white-space: nowrap;
  }
</style>
</head>
<body>
<main class="menu">
  <header class="brand">
    <span class="brand-mark"></span>
    <div class="brand-text">
      <span class="brand-name">Tinker's Lamp</span>
      <span class="brand-sub">PUB &amp; RESTAURANT</span>
    </div>
  </header>
  <div class="header-rule"></div>

  <section class="col-left">
    <h2 class="section-title" style="top:116px;left:60px;">BURGERS <span class="small">AND</span><br>SANDWICHES</h2>

    <article class="item" style="top:227px;">
      <h3 class="item-name">Chicken Sandwich</h3>
      <span class="price"><sup>$</sup>12</span>
      <p class="item-desc">Chicken Breast, Applewood Bacon, Butter Lettuce, White<br>Cheddar, Avocado and Tomato Served on Sourdough Bread</p>
    </article>
    <div class="divider" style="top:300px;"></div>

    <article class="item" style="top:319px;">
      <h3 class="item-name">Buttermilk Fried Chicken</h3>
      <span class="price"><sup>$</sup>13</span>
      <p class="item-desc">Coleslaw, Provolone, Tomato, and a Spiced Mayonnaise<br>on a Pretzel Roll</p>
    </article>
    <div class="divider" style="top:392px;"></div>

    <article class="item" style="top:411px;">
      <h3 class="item-name">Short Rib Sandwich</h3>
      <span class="price"><sup>$</sup>13</span>
      <p class="item-desc">Beef Shorts, Mayo, Tomato, Caramelized Onions, Arugula,<br>Pepper Jack Cheese Served on Sourdough Bread</p>
    </article>
    <div class="divider" style="top:486px;"></div>

    <article class="item" style="top:504px;">
      <h3 class="item-name">Grilled Cheese Sandwich</h3>
      <span class="price"><sup>$</sup>10</span>
      <p class="item-desc">Cheese, Provolone and Cheddar Cheese</p>
    </article>
    <div class="divider" style="top:558px;"></div>

    <article class="item" style="top:576px;">
      <h3 class="item-name">Tinker's Lamp Burger</h3>
      <span class="price"><sup>$</sup>14</span>
      <p class="item-desc">Sharp Cheddar, Arugula, Roasted Shallots, Bacon<br>Jam with Malt Aioli</p>
    </article>
    <div class="divider" style="top:652px;"></div>

    <article class="item" style="top:669px;">
      <h3 class="item-name">The Truffle Burger</h3>
      <span class="price"><sup>$</sup>15</span>
      <p class="item-desc">Caramelized Onions, Arugula, Truffle Pecorino,<br>Truffle Mayo and Truffle Fries</p>
    </article>
    <div class="divider" style="top:748px;"></div>

    <article class="item" style="top:770px;">
      <h3 class="item-name">The Sloppy Joe</h3>
      <span class="price"><sup>$</sup>10</span>
      <p class="item-desc">Shredded Lettuce and Sharp Cheddar</p>
    </article>
    <div class="divider" style="top:826px;"></div>

    <article class="item" style="top:846px;">
      <h3 class="item-name">Veggie Burger</h3>
      <span class="price"><sup>$</sup>12</span>
      <p class="item-desc">Concoction of kale, Tomato, Avocado, Sharp Cheddar<br>with a Balsamic Reduction</p>
    </article>
    <div class="divider" style="top:923px;"></div>

    <article class="item" style="top:944px;">
      <h3 class="item-name">Flat Iron Steak Sandwich</h3>
      <span class="price"><sup>$</sup>16</span>
      <p class="item-desc">Arugula, Peppers, Fontina, Onion and Mayo</p>
    </article>
    <div class="divider" style="top:1002px;"></div>

    <article class="item" style="top:1022px;">
      <h3 class="item-name">Chicken Spinach Wrap</h3>
      <span class="price"><sup>$</sup>10</span>
      <p class="item-desc" style="white-space:nowrap;">Chicken, Bacon, Lettuce, Tomato, Avocado, Ranch and Mayo</p>
    </article>

    <article class="item" style="top:1100px;">
      <h3 class="item-name">Fried Chicken Sliders(4)</h3>
      <span class="price"><sup>$</sup>12</span>
      <p class="item-desc">Coleslaw, Lime Sriracha Sauce</p>
    </article>
  </section>

  <section class="col-right">
    <h2 class="section-title" style="top:116px;left:474px;">BIG DOG<br>BITES</h2>

    <article class="item" style="top:227px;">
      <h3 class="item-name">Atlantic Cod Fish N' Chips</h3>
      <span class="price"><sup>$</sup>15</span>
      <p class="item-desc">House Tartar Sauce, Vinegar and Lemon Wedge</p>
    </article>
    <div class="divider" style="top:281px;width:95px;"></div>

    <article class="item" style="top:299px;">
      <h3 class="item-name">Oven Roasted ½ Roasted Chicken</h3>
      <span class="price"><sup>$</sup>16</span>
      <p class="item-desc">Boneless Chicken, Broccolini, Fingerling Potatoes,<br>Topped with Chimichurri Sauce</p>
    </article>
    <div class="divider" style="top:372px;width:95px;"></div>

    <article class="item" style="top:389px;">
      <h3 class="item-name">Black Mussels</h3>
      <span class="price"><sup>$</sup>17</span>
      <p class="item-desc">Tequila Chipotle Sauce, Cilantro and Cherry Tomatoes</p>
    </article>
    <div class="divider" style="top:447px;width:95px;"></div>

    <article class="item" style="top:464px;">
      <h3 class="item-name">Pan Seared Salmon</h3>
      <span class="price"><sup>$</sup>19</span>
      <p class="item-desc" style="white-space:nowrap;">Sushi Grade Salmon, Spaghetti Squash, Zucchini, Cherry Tomatoes<br>In a Lemon Caper Beurre Blanc</p>
    </article>
    <div class="divider" style="top:541px;width:95px;"></div>

    <article class="item" style="top:560px;">
      <h3 class="item-name">Flat Iron Steak</h3>
      <span class="price"><sup>$</sup>22</span>
      <p class="item-desc">French Fries, Baby Arugula in a Light peppercorn Sauce</p>
    </article>

    <svg class="frame" width="927" height="1200" aria-hidden="true">
      <g fill="none" stroke="var(--tan)" stroke-width="1.5" stroke-dasharray="1.5 1.5">
        <path d="M470 663 H456 V1163 H927"/>
        <path d="M758 663 H927"/>
      </g>
    </svg>

    <h2 class="section-title" style="top:640px;left:474px;">FLATBREADS</h2>

    <article class="item" style="top:698px;">
      <h3 class="item-name">Margherita</h3>
      <span class="price"><sup>$</sup>12</span>
      <p class="item-desc">Fresh Mozzarella, Roma Tomatoes and Fresh Italian Basil</p>
    </article>
    <div class="divider" style="top:754px;"></div>

    <article class="item" style="top:771px;">
      <h3 class="item-name">Vegetarian</h3>
      <span class="price"><sup>$</sup>13</span>
      <p class="item-desc">Brussel Sprouts, Peppers, Onions, Zucchini, Goat Cheese,<br>Smoked Mozzarella Topped with a Balsamic Reduction</p>
    </article>
    <div class="divider" style="top:846px;"></div>

    <article class="item" style="top:863px;">
      <h3 class="item-name">Prosciutto &amp; Arugula</h3>
      <span class="price"><sup>$</sup>14</span>
      <p class="item-desc">Red Onion, Parmesan, Mozzarella</p>
    </article>
    <div class="divider" style="top:924px;"></div>

    <article class="item" style="top:940px;">
      <h3 class="item-name">Portobello &amp; Truffle</h3>
      <span class="price"><sup>$</sup>14</span>
      <p class="item-desc">Portobello White Mushroom, Fontina, Drizzled with Truffle Oil</p>
    </article>
    <div class="divider" style="top:1003px;"></div>

    <article class="item" style="top:1022px;">
      <h3 class="item-name">Chicken Tikka Masala</h3>
      <span class="price"><sup>$</sup>22</span>
      <p class="item-desc">Tandoori Chicken, Fontini and Raita</p>
    </article>
    <div class="divider" style="top:1082px;"></div>

    <article class="item" style="top:1100px;">
      <h3 class="item-name">The Tinker's Lamp</h3>
      <span class="price"><sup>$</sup>13</span>
      <p class="item-desc">Meatballs, Sausage, Chorizo, Mozzarella and Fresen</p>
    </article>
  </section>

  <aside class="event-band" aria-label="Weekly events">
    <span>BEER PONG MON</span>
    <span>TRIVIA TUE</span>
    <span>TACO TUE</span>
    <span>WHISKEY WED</span>
    <span>KARAOKE SAT</span>
  </aside>
</main>
</body>
</html>
```